Black Car Limousine transportation business in Naples Florida

Always stand for my reliability and RVD stands for Love, K and M are the first initials of my children's names. It should show professionalism and a dedication to customer service. We keep our clients identities private. Show our professionalism. We are Black car Black tie company. We service transportation on a reserve basis to and from residents, airports, casinos, hotels,

Target Market(s)

It is a Private car service. High end clients. Businesses, Celebrity and athletes. Service to airports, hotels, special events.

Industry/Entity Type

Business

Contact Information for Business Card

A pearl metallic or Luster card. Standard business card size. Would like the name, Company email, show we take credit cards and phone number. Currently I don't have a website but will like to add later.

Logo Text

STEADFAST RVD TRANSPORTATION

Font styles to use
Serif

Colors
eaeaea
000000

Requirements
Must have
• Must have Company email, show we take credit cards and phone number. Currently I don't have a website but will like to add later.
Nice to have
• Would like to stay with a black and white theme. Open to some color trim.
Should not have
• Open to suggestions

```html
<!DOCTYPE html>
<html lang="en">
<head>
<meta charset="utf-8">
<title>Steadfast RVD Transportation – Business Card</title>
<link rel="stylesheet" href="https://fonts.googleapis.com/css2?family=Open+Sans:ital,wght@0,400;0,600;0,700;1,700&display=swap">
<style>
  :root {
    --stage: #c9c9c9;
    --card-light: #ffffff;
    --card-dark: #000000;
    --ink: #111111;
    --ink-soft: #4a4a4a;
    --mark-grey: #9a9a9a;
    --photo-dark-a: #1a1a1a;
    --photo-dark-b: #5a5a5a;
    --photo-faint-a: #ffffff;
    --photo-faint-b: #e4e4e4;
    --white: #ffffff;
  }
  * { margin: 0; padding: 0; box-sizing: border-box; }
  html, body {
    width: 1105px; height: 1200px; overflow: hidden;
    background: var(--stage);
    font-family: "Open Sans", Arial, sans-serif;
  }
  .card {
    position: absolute; left: 193px; width: 719px; height: 410px;
    box-shadow: 0 4px 10px rgba(0,0,0,0.35);
    overflow: hidden;
  }
  .card--front { top: 167px; background: var(--card-light); }
  .card--back { top: 622px; background: var(--card-dark); }

  .vehicle-photo {
    position: absolute; border-radius: 10px;
    background: linear-gradient(180deg, var(--photo-dark-b), var(--photo-dark-a) 70%);
  }
  .vehicle-photo--faint {
    left: 297px; top: 206px; width: 422px; height: 204px; border-radius: 60px 0 0 0;
    background: linear-gradient(135deg, var(--photo-faint-a) 20%, var(--photo-faint-b));
  }
  .card--front .vehicle-photo--logo { left: 52px; top: 92px; width: 157px; height: 66px; }
  .card--back .vehicle-photo--logo { left: 138px; top: 178px; width: 175px; height: 72px; }

  .brand-name {
    position: absolute; color: var(--mark-grey); font-weight: 700;
    line-height: 1.1; letter-spacing: 1px;
  }
  .card--front .brand-name { left: 221px; top: 92px; font-size: 22px; }
  .card--back .brand-name { left: 328px; top: 178px; font-size: 24px; }
  .brand-name span { display: block; }

  .contact-list { position: absolute; left: 52px; top: 280px; list-style: none; }
  .contact-list li {
    display: flex; align-items: center; height: 28px;
    font-size: 19px; color: var(--ink-soft);
  }
  .contact-list svg { width: 18px; height: 18px; margin-right: 10px; fill: var(--ink); }

  .person { position: absolute; right: 55px; top: 292px; text-align: right; }
  .person__name { font-size: 24px; font-weight: 600; color: var(--ink); letter-spacing: 0.5px; }
  .person__role { font-size: 19px; color: var(--ink-soft); }

  .payment-note {
    position: absolute; left: 0; right: 0; top: 332px;
    display: flex; justify-content: center; align-items: center; gap: 8px;
    color: var(--white); font-size: 19px; font-weight: 700; font-style: italic;
  }
  .payment-note svg { width: 24px; height: 18px; }
</style>
</head>
<body>
  <section class="card card--front">
    <div class="vehicle-photo vehicle-photo--faint" role="img" aria-label="Faded photo of a black luxury SUV"></div>
    <div class="vehicle-photo vehicle-photo--logo" role="img" aria-label="Photo of a black luxury SUV"></div>
    <div class="brand-name"><span>STEADFAST</span><span>RVD</span><span>TRANSPORTATION</span></div>

    <ul class="contact-list">
      <li><svg viewBox="0 0 24 24"><path d="M6.6 10.8a15 15 0 0 0 6.6 6.6l2.2-2.2a1 1 0 0 1 1-.25 11.4 11.4 0 0 0 3.6.57 1 1 0 0 1 1 1V20a1 1 0 0 1-1 1A17 17 0 0 1 3 4a1 1 0 0 1 1-1h3.5a1 1 0 0 1 1 1c0 1.25.2 2.45.57 3.57a1 1 0 0 1-.25 1z"/></svg>555 014 2273</li>
      <li><svg viewBox="0 0 24 24"><path d="M2 5h20v14H2z M2 5l10 8 10-8" fill="none" stroke="#111" stroke-width="2"/></svg>hello@steadfastrvd.com</li>
      <li><svg viewBox="0 0 24 24"><circle cx="12" cy="12" r="10"/><path d="M2 12h20M12 2c3 3 3 17 0 20M12 2c-3 3-3 17 0 20" fill="none" stroke="#fff" stroke-width="1.5"/></svg>www.steadfastrvd.com</li>
    </ul>

    <div class="person">
      <div class="person__name">DANIEL REEVES</div>
      <div class="person__role">CEO/Founder</div>
    </div>
  </section>

  <section class="card card--back">
    <div class="vehicle-photo vehicle-photo--logo" role="img" aria-label="Photo of a black luxury SUV"></div>
    <div class="brand-name"><span>STEADFAST</span><span>RVD</span><span>TRANSPORTATION</span></div>
    <p class="payment-note">
      <svg viewBox="0 0 24 18"><rect x="1" y="1" width="22" height="16" rx="2" fill="#fff"/><rect x="1" y="5" width="22" height="3" fill="#000"/><rect x="4" y="11" width="7" height="2" fill="#000"/></svg>
      We accept credit cards
    </p>
  </section>
</body>
</html>
```